Business Card Design Project for Heron Lending

Hello there,

We are looking for a business card design for our new Heron Lending car financing company. We are looking for a business card that will include:

- An address
- Telephone number and extension
- Employee Name
- Employee Title
- Our logo and name clearly visible

We are including our logo with this writeup, we are looking to convey friendliness, trus and memorability. Colors and everything else is up to you.

Target Market(s)

18-34 year old males and females

Industry/Entity Type

Business

```html
<!DOCTYPE html>
<html lang="en">
<head>
<meta charset="utf-8">
<title>Heron Lending — Business Card</title>
<link href="https://fonts.googleapis.com/css2?family=Open+Sans:wght@400;600;700&display=swap" rel="stylesheet">
<style>
  :root {
    --backdrop: #eeeeee;
    --card-paper: #ecebe9;
    --brand-navy: #033b53;
    --brand-ink: #1d1a19;
    --text-light: #ffffff;
  }
  * { box-sizing: border-box; margin: 0; padding: 0; }
  html, body {
    width: 1200px;
    height: 675px;
    overflow: hidden;
    background: var(--backdrop);
    font-family: "Open Sans", Arial, sans-serif;
  }
  .stage {
    position: relative;
    width: 1200px;
    height: 675px;
    display: flex;
    align-items: center;
    justify-content: center;
    gap: 60px;
  }
  .card {
    position: relative;
    width: 520px;
    height: 297px;
    border-radius: 3px;
    overflow: hidden;
    box-shadow: 0 6px 18px rgba(0, 0, 0, 0.12);
  }

  /* Back side */
  .card-back {
    background: var(--brand-navy);
    display: flex;
    align-items: center;
    justify-content: center;
  }
  .card-back .brand-name {
    color: var(--text-light);
    font-weight: 600;
    font-size: 40px;
    letter-spacing: 0.02em;
  }

  /* Front side */
  .card-front { background: var(--card-paper); }
  .card-front .bands {
    position: absolute;
    inset: 0;
  }
  .band-navy { fill: var(--brand-navy); }
  .band-ink { fill: var(--brand-ink); }

  .card-front .brand-name {
    position: absolute;
    top: 62px;
    right: 34px;
    color: var(--brand-navy);
    font-weight: 600;
    font-size: 26px;
    letter-spacing: 0.02em;
  }
  .person {
    position: absolute;
    left: 40px;
    top: 108px;
    color: var(--brand-navy);
  }
  .person-name {
    font-weight: 700;
    font-size: 17px;
    line-height: 1.2;
  }
  .person-title {
    font-weight: 400;
    font-size: 13px;
    margin-top: 2px;
    padding-left: 10px;
  }
  .contact {
    position: absolute;
    left: 40px;
    bottom: 30px;
    list-style: none;
    color: var(--text-light);
    font-size: 13px;
    line-height: 1.55;
  }
  .contact li {
    display: flex;
    align-items: center;
    gap: 8px;
  }
  .contact svg {
    width: 11px;
    height: 11px;
    fill: var(--text-light);
    flex: none;
  }
</style>
</head>
<body>
  <main class="stage">
    <section class="card card-back" aria-label="Card back">
      <span class="brand-name">Heron Lending</span>
    </section>

    <section class="card card-front" aria-label="Card front">
      <svg class="bands" viewBox="0 0 520 297" preserveAspectRatio="none" aria-hidden="true">
        <polygon class="band-ink" points="395,138 520,138 520,200 430,200"/>
        <polygon class="band-navy" points="0,172 395,172 430,200 520,200 520,297 0,297"/>
      </svg>

      <span class="brand-name">Heron Lending</span>

      <div class="person">
        <p class="person-name">Your Long Name</p>
        <p class="person-title">Your Title</p>
      </div>

      <ul class="contact">
        <li>
          <svg viewBox="0 0 24 24" aria-hidden="true"><path d="M6.6 10.8a15.1 15.1 0 0 0 6.6 6.6l2.2-2.2a1 1 0 0 1 1-.25 11.4 11.4 0 0 0 3.6.57 1 1 0 0 1 1 1V20a1 1 0 0 1-1 1A17 17 0 0 1 3 4a1 1 0 0 1 1-1h3.5a1 1 0 0 1 1 1c0 1.25.2 2.45.57 3.6a1 1 0 0 1-.25 1z"/></svg>
          <span>00.00.00.0000</span>
        </li>
        <li>
          <svg viewBox="0 0 24 24" aria-hidden="true"><path d="M12 2a7 7 0 0 0-7 7c0 5.25 7 13 7 13s7-7.75 7-13a7 7 0 0 0-7-7zm0 9.5A2.5 2.5 0 1 1 12 6.5a2.5 2.5 0 0 1 0 5z"/></svg>
          <span>Your Commercial or office address</span>
        </li>
      </ul>
    </section>
  </main>
</body>
</html>
```